Commercial Refrigeration Service Company requires stylish and fresh looking flyer.

We need a flyer to hand out to new customers. It should have a photo and our branding, list all the services that are offered and our contact details.
We would like two flyers to be supplied, both identical though one offering a discount until July ( Half Price Service Fee ). The flyer should be clear, interesting and in similar colours to the branding package supplied.
Please look at our website for information about the services on offer:
www.brisko-coolworks.com.au

Target Market(s)

Cafes, bars, restaurants, pubs ect.

Font styles to use
Other font styles liked:
• Font package provided

Colors
85cae6
ffffff
333333

Requirements
Must have
• - The photo provided.
• - The company logo.
• - Similar feel to the website & business card.
• - Smooth layout and clear to understand.
Should not have
• - No clunky badges or prints.

```html
<!DOCTYPE html>
<html lang="en">
<head>
<meta charset="utf-8">
<title>Brisko Commercial Refrigeration Flyer</title>
<link rel="stylesheet" href="https://fonts.googleapis.com/css2?family=Encode+Sans+Condensed:wght@300;400&family=Open+Sans:wght@400;700&display=swap">
<style>
  :root {
    --brand-blue: #5bc2ea;
    --ink: #333333;
    --white: #ffffff;
    --footer: #262828;
    --paper-top: #f5f5f5;
    --paper-bottom: #e2e2e2;
    --icon-fill: #8c8d8f;
    --backdrop: #7a7a7a;
  }
  * { box-sizing: border-box; margin: 0; padding: 0; }
  html, body { width: 1200px; height: 1146px; overflow: hidden; background: var(--backdrop); }
  .flyer {
    position: absolute; left: 224px; top: 40px; width: 752px; height: 1066px;
    background: linear-gradient(var(--paper-top), var(--paper-bottom));
    overflow: hidden;
  }
  .hero-photo {
    position: absolute; left: 0; top: 0; width: 752px; height: 357px;
    background: linear-gradient(180deg, #8fb7d8 0%, #b8cfe0 28%, #8c97a3 50%, #6f747a 72%, #5a5d61 100%);
  }
  .brand-band {
    position: absolute; left: 0; top: 357px; width: 752px; height: 149px;
    background: var(--brand-blue);
    display: flex; align-items: center; justify-content: center;
  }
  .brand-name {
    font-family: "Encode Sans Condensed", sans-serif; font-weight: 300;
    font-size: 58px; line-height: 1; color: var(--footer);
  }
  .business-line {
    position: absolute; left: 0; right: 0; top: 536px; text-align: center;
    font-family: "Encode Sans Condensed", sans-serif; font-weight: 300;
    font-size: 24px; color: var(--ink);
  }
  .offer { position: absolute; left: 0; right: 0; top: 630px; text-align: center; color: var(--brand-blue); font-family: "Encode Sans Condensed", sans-serif; font-weight: 300; }
  .offer-title { font-size: 41px; line-height: 46px; }
  .offer-detail { font-size: 25.5px; line-height: 30px; }
  .divider { position: absolute; left: 270px; top: 735px; width: 200px; height: 1px; background: var(--brand-blue); }
  .services { position: absolute; left: 0; right: 0; top: 762px; text-align: center; font-family: "Encode Sans Condensed", sans-serif; font-weight: 300; }
  .services-title { color: var(--brand-blue); font-size: 27px; line-height: 34px; }
  .services-list { color: var(--ink); font-size: 21.5px; line-height: 25px; }
  .service-ticks { position: absolute; left: 111px; top: 879px; display: flex; gap: 11px; }
  .service-ticks svg { width: 66px; height: 66px; }
  .contact-footer { position: absolute; left: 0; top: 940px; width: 752px; height: 126px; background: var(--footer); text-align: center; font-family: "Open Sans", sans-serif; }
  .contact-line { color: var(--white); font-size: 21.5px; margin-top: 36px; }
  .web-line { color: var(--brand-blue); font-size: 21px; font-weight: 700; margin-top: 3px; }
</style>
</head>
<body>
<main class="flyer">
  <div class="hero-photo" role="img" aria-label="Photo of a technician standing beside the company service ute parked by the beach"></div>

  <section class="brand-band">
    <div class="brand-name">Brisko</div>
  </section>

  <div class="business-line">Commercial Refrigeration</div>

  <section class="offer">
    <div class="offer-title">DISCOUNT UNTIL JULY</div>
    <div class="offer-detail">PAY ONLY HALF PRICE OF THE SERVICE FEE</div>
  </section>

  <div class="divider"></div>

  <section class="services">
    <div class="services-title">SERVICES</div>
    <div class="services-list">Commercial Refrigeration | Ice Makers | Beer Systems<br>Electrical | 24hr Service | Sales | Installation</div>
  </section>

  <div class="service-ticks" aria-hidden="true">
    <svg viewBox="0 0 66 66"><circle cx="33" cy="33" r="32" fill="var(--icon-fill)"/><path d="M22 34l8 8 15-17" fill="none" stroke="#fff" stroke-width="3" stroke-linecap="round" stroke-linejoin="round"/></svg>
    <svg viewBox="0 0 66 66"><circle cx="33" cy="33" r="32" fill="var(--icon-fill)"/><path d="M22 34l8 8 15-17" fill="none" stroke="#fff" stroke-width="3" stroke-linecap="round" stroke-linejoin="round"/></svg>
    <svg viewBox="0 0 66 66"><circle cx="33" cy="33" r="32" fill="var(--icon-fill)"/><path d="M22 34l8 8 15-17" fill="none" stroke="#fff" stroke-width="3" stroke-linecap="round" stroke-linejoin="round"/></svg>
    <svg viewBox="0 0 66 66"><circle cx="33" cy="33" r="32" fill="var(--icon-fill)"/><path d="M22 34l8 8 15-17" fill="none" stroke="#fff" stroke-width="3" stroke-linecap="round" stroke-linejoin="round"/></svg>
    <svg viewBox="0 0 66 66"><circle cx="33" cy="33" r="32" fill="var(--icon-fill)"/><path d="M22 34l8 8 15-17" fill="none" stroke="#fff" stroke-width="3" stroke-linecap="round" stroke-linejoin="round"/></svg>
    <svg viewBox="0 0 66 66"><circle cx="33" cy="33" r="32" fill="var(--icon-fill)"/><path d="M22 34l8 8 15-17" fill="none" stroke="#fff" stroke-width="3" stroke-linecap="round" stroke-linejoin="round"/></svg>
    <svg viewBox="0 0 66 66"><circle cx="33" cy="33" r="32" fill="var(--icon-fill)"/><path d="M22 34l8 8 15-17" fill="none" stroke="#fff" stroke-width="3" stroke-linecap="round" stroke-linejoin="round"/></svg>
  </div>

  <footer class="contact-footer">
    <div class="contact-line">0400 271 846 &nbsp;| info@brisko-coolworks.com.au</div>
    <div class="web-line">WWW.BRISKO-COOLWORKS.COM.AU</div>
  </footer>
</main>
</body>
</html>
```